printing company neeeds a trifold design

I need a trifold brochure (8.5 x 11) flat size, then folded to a trifold that will highlight about a dozen of my most popular products. Should be modern, with just enough of a sales tool. I attached a few thing that I have but looking for something special. I can supply images or you can use place holders?
Updates

The brochure with the "eye" on the front panel is my most current trifold and you can follow that for most of the content. I might edit that later on

Please DO NOT copy my design. Looking for something fresh, new and interesting. I added my old one to show some content and images.
Thanks all!!!!

good morning I am looking for something different. Fresh, modern, clean (neeeds to be cohesive and able to be branded for social media, postcards etc.) and No "eye" or just a small one. . You can use some of the pics and some of the content. This needs to be sales piece I sent out to prospective clients.
Show that we are professional, personal and do great work. 3rd generation printer that is responsive and reaches out to all that respond. All types of Printing, Large format like signs and banners, Realesate, small biz, trade show products look at kornbluthpress.com

Designs look the same

Target Market(s)

Small business, real eststate firms, local business, professionals

Industry/Entity Type

I am in the printing and sign business... 2 of my websites are kornbluthpress.com and kornbluthtypeworks.com

Requirements
Must have
• a front panel with contact info and company logo that I can send over, a panel about my company and images
Nice to have
• something stylish, easy to read with impact. Needs to be something people will wanty to knao more abouit and top reach out
Should not have
• The same look as what I sent over.

```html
<!DOCTYPE html>
<html lang="en">
<head>
<meta charset="utf-8">
<title>Kornbluth Press – Trifold Inside</title>
<link href="https://fonts.googleapis.com/css2?family=Saira+Condensed:wght@400;600;700&family=Montserrat:wght@400&display=swap" rel="stylesheet">
<style>
  :root {
    --paper: #ffffff;
    --ink: #1e1f21;
    --panel-dark: #1c1e20;
    --accent-cyan: #3ec9f2;
    --band-teal: #5ed9d6;
    --band-sky: #5cc8f5;
    --band-blue: #4aa6f0;
    --accent-magenta: #f21fd2;
    --text-light: #ffffff;
  }
  * { margin: 0; padding: 0; box-sizing: border-box; }
  html, body { width: 1200px; height: 927px; overflow: hidden; background: var(--paper); }
  .sheet { position: relative; width: 1200px; height: 927px; overflow: hidden; background: var(--paper); }
  .panel { position: absolute; top: 0; height: 927px; }
  .panel-about { left: 0; width: 398px; }
  .panel-services { left: 398px; width: 397px; background: var(--panel-dark); }
  .panel-showcase { left: 795px; width: 405px; }
  .art { position: absolute; left: 0; top: 0; }

  .headline {
    position: absolute;
    font-family: "Saira Condensed", sans-serif;
    font-weight: 700;
    color: var(--text-light);
    line-height: 1;
    letter-spacing: 0.5px;
  }
  .headline-printing { left: 38px; top: 234px; font-size: 66px; }
  .headline-signs { left: 58px; top: 572px; font-size: 66px; line-height: 0.98; }

  .about-title {
    position: absolute; left: 41px; top: 604px;
    font-family: "Saira Condensed", sans-serif;
    font-size: 40px; font-weight: 400; color: var(--ink); line-height: 1;
  }
  .about-title strong { font-weight: 700; }
  .about-copy {
    position: absolute; left: 42px; top: 655px; width: 325px;
    font-family: "Montserrat", sans-serif; font-size: 13.6px; line-height: 22.5px;
    color: var(--ink); text-align: justify;
  }
  .about-copy p + p { margin-top: 22.5px; }

  .services-title {
    position: absolute; left: 36px; top: 44px;
    font-family: "Saira Condensed", sans-serif; font-weight: 700;
    font-size: 42px; color: var(--accent-cyan); line-height: 1;
  }
  .services-list {
    position: absolute; left: 36px; top: 116px; list-style: none;
    font-family: "Montserrat", sans-serif; font-size: 15.6px; color: var(--text-light);
  }
  .services-list li { display: flex; align-items: center; height: 36.4px; }
  .services-list svg { width: 16px; height: 20px; margin-right: 14px; flex: none; }
  .services-photo {
    position: absolute; left: 23px; top: 751px; width: 349px; height: 176px;
    background: linear-gradient(90deg, #2a2a2a 0%, #3b3530 34%, #f1ece2 36%, #e8ddc8 64%, #c3263a 66%, #5a3b7a 100%);
  }
</style>
</head>
<body>
<main class="sheet">

  <section class="panel panel-about">
    <svg class="art" width="398" height="927" viewBox="0 0 398 927" role="img" aria-label="Photo of fanned colour swatch cards in teal and blue">
      <defs>
        <linearGradient id="swatch-band-left" x1="0" y1="0" x2="1" y2="1">
          <stop offset="0" stop-color="var(--band-teal)"/>
          <stop offset="0.5" stop-color="var(--band-sky)"/>
          <stop offset="1" stop-color="var(--band-blue)"/>
        </linearGradient>
      </defs>
      <polygon points="0,31 398,171 398,614 0,475" fill="url(#swatch-band-left)"/>
    </svg>
    <h1 class="headline headline-printing">PRINTING</h1>
    <h2 class="about-title">ABOUT <strong>US</strong></h2>
    <div class="about-copy">
      <p>We are Kornbluth Press, your expert printing source for everything from business cards to brochures, large format printing, signs &amp; banners We have you covered.</p>
      <p>For 3 generations, Kornbluth Press has been serving professionals, businesses and organizations like yours, helping them grow their brand and prosper</p>
    </div>
  </section>

  <section class="panel panel-services">
    <h2 class="services-title">OUR SERVICES</h2>
    <ul class="services-list">
      <li><svg viewBox="0 0 16 20"><path d="M4 3 L4 17 L7.5 13.5 L10 19 L12 18 L9.5 12.5 L14 12.5 Z" fill="var(--accent-cyan)"/></svg>Business Cards</li>
      <li><svg viewBox="0 0 16 20"><path d="M4 3 L4 17 L7.5 13.5 L10 19 L12 18 L9.5 12.5 L14 12.5 Z" fill="var(--accent-cyan)"/></svg>Brochures &amp; Menus</li>
      <li><svg viewBox="0 0 16 20"><path d="M4 3 L4 17 L7.5 13.5 L10 19 L12 18 L9.5 12.5 L14 12.5 Z" fill="var(--accent-cyan)"/></svg>Postcards</li>
      <li><svg viewBox="0 0 16 20"><path d="M4 3 L4 17 L7.5 13.5 L10 19 L12 18 L9.5 12.5 L14 12.5 Z" fill="var(--accent-cyan)"/></svg>Presentation Folders</li>
      <li><svg viewBox="0 0 16 20"><path d="M4 3 L4 17 L7.5 13.5 L10 19 L12 18 L9.5 12.5 L14 12.5 Z" fill="var(--accent-cyan)"/></svg>Booklets &amp; Catalogs</li>
      <li><svg viewBox="0 0 16 20"><path d="M4 3 L4 17 L7.5 13.5 L10 19 L12 18 L9.5 12.5 L14 12.5 Z" fill="var(--accent-cyan)"/></svg>Raffle Tickets</li>
      <li><svg viewBox="0 0 16 20"><path d="M4 3 L4 17 L7.5 13.5 L10 19 L12 18 L9.5 12.5 L14 12.5 Z" fill="var(--accent-cyan)"/></svg>Letterpress Printing</li>
      <li><svg viewBox="0 0 16 20"><path d="M4 3 L4 17 L7.5 13.5 L10 19 L12 18 L9.5 12.5 L14 12.5 Z" fill="var(--accent-cyan)"/></svg>Wedding Invitations</li>
      <li><svg viewBox="0 0 16 20"><path d="M4 3 L4 17 L7.5 13.5 L10 19 L12 18 L9.5 12.5 L14 12.5 Z" fill="var(--accent-cyan)"/></svg>Save the Date Items</li>
      <li><svg viewBox="0 0 16 20"><path d="M4 3 L4 17 L7.5 13.5 L10 19 L12 18 L9.5 12.5 L14 12.5 Z" fill="var(--accent-cyan)"/></svg>Business Announcements</li>
      <li><svg viewBox="0 0 16 20"><path d="M4 3 L4 17 L7.5 13.5 L10 19 L12 18 L9.5 12.5 L14 12.5 Z" fill="var(--accent-cyan)"/></svg>Greeting Cards</li>
      <li><svg viewBox="0 0 16 20"><path d="M4 3 L4 17 L7.5 13.5 L10 19 L12 18 L9.5 12.5 L14 12.5 Z" fill="var(--accent-cyan)"/></svg>Signs &amp; Banners</li>
      <li><svg viewBox="0 0 16 20"><path d="M4 3 L4 17 L7.5 13.5 L10 19 L12 18 L9.5 12.5 L14 12.5 Z" fill="var(--accent-cyan)"/></svg>Retractable Banners</li>
      <li><svg viewBox="0 0 16 20"><path d="M4 3 L4 17 L7.5 13.5 L10 19 L12 18 L9.5 12.5 L14 12.5 Z" fill="var(--accent-cyan)"/></svg>A-Frame Signs &amp; Flags</li>
      <li><svg viewBox="0 0 16 20"><path d="M4 3 L4 17 L7.5 13.5 L10 19 L12 18 L9.5 12.5 L14 12.5 Z" fill="var(--accent-cyan)"/></svg>Event Tents</li>
      <li><svg viewBox="0 0 16 20"><path d="M4 3 L4 17 L7.5 13.5 L10 19 L12 18 L9.5 12.5 L14 12.5 Z" fill="var(--accent-cyan)"/></svg>Posters</li>
      <li><svg viewBox="0 0 16 20"><path d="M4 3 L4 17 L7.5 13.5 L10 19 L12 18 L9.5 12.5 L14 12.5 Z" fill="var(--accent-cyan)"/></svg>Canvas Prints and more</li>
    </ul>
    <div class="services-photo" role="img" aria-label="Photo of printed rack cards and menus laid on kraft paper"></div>
  </section>

  <section class="panel panel-showcase">
    <svg class="art" width="405" height="927" viewBox="0 0 405 927">
      <defs>
        <linearGradient id="swatch-band-right" x1="0" y1="0" x2="1" y2="1">
          <stop offset="0" stop-color="var(--band-teal)"/>
          <stop offset="0.45" stop-color="var(--band-sky)"/>
          <stop offset="1" stop-color="#6ad6f7"/>
        </linearGradient>
        <linearGradient id="cards-a" x1="0" y1="0" x2="1" y2="1">
          <stop offset="0" stop-color="#d9d4c6"/>
          <stop offset="0.5" stop-color="#2c6f8a"/>
          <stop offset="1" stop-color="#3fb93a"/>
        </linearGradient>
        <linearGradient id="cards-b" x1="0" y1="0" x2="1" y2="1">
          <stop offset="0" stop-color="#f6f3ea"/>
          <stop offset="0.45" stop-color="#f4b01e"/>
          <stop offset="1" stop-color="#2f4fc4"/>
        </linearGradient>
        <linearGradient id="cards-c" x1="0" y1="0" x2="1" y2="1">
          <stop offset="0" stop-color="#2a2a2a"/>
          <stop offset="0.5" stop-color="#3aa8d8"/>
          <stop offset="1" stop-color="#26a33a"/>
        </linearGradient>
      </defs>
      <polygon points="0,341 405,484 405,927 0,786" fill="url(#swatch-band-right)" role="img" aria-label="Photo of fanned colour swatch cards in teal and blue"/>
      <polygon points="315,440 405,409 405,478" fill="var(--accent-magenta)"/>
      <polygon points="107,22 199,75 199,182 107,235 15,182 15,75" fill="url(#cards-a)" role="img" aria-label="Photo of assorted printed business cards"/>
      <polygon points="301,22 393,75 393,182 301,235 209,182 209,75" fill="url(#cards-b)" role="img" aria-label="Photo of printed school flyer and promotional cards"/>
      <polygon points="206,193 298,246 298,353 206,406 114,353 114,246" fill="url(#cards-c)" role="img" aria-label="Photo of printed business cards on a corkboard"/>
    </svg>
    <h2 class="headline headline-signs">SIGNS<br>INVITATIONS</h2>
  </section>

</main>
</body>
</html>
```